Holiday Rental Company Flyer Design (DL not A5)

Note from Brandloom Administration: The category sizing selected is A5, however the project requires DL sized artwork. Please refer to the DL template link below while the 'Special Requirements' are updated accordingly.

Project Brief:
We need a double sided DL flyer designed for an up market Holiday Rental Company that portrays a personalised approach to property management. These are to be used for letter box drops to homes we're specifically targeting so the design should be modern, complimentary colour palette, uncluttered & visually appealing.

Please Download the DL Template from Quillora here: http://www.quillora.com.au/ql/ns/propath/UploadResources.aspx?selectedTab=0?pfid=KMT&pf_id=KMT&xnav=easypath-upload-image#Templates

Target Market(s)

Wealthy Home Owners

Industry/Entity Type

It Company

Other font styles liked:
• Avant Garde Extra Light & Demi

Colors
33b8a4

Requirements
Must have
• DL Flyer sizes (210mm width x 99mm width, plus 3mm bleed)
• Front: Logo, Main Image & Grab
• Back: Contact Details & Brief Description of our business
• Images: Ideally the main image should be the house with the pool but alternatively a lifestyle images could also be used.
Nice to have
• A creative designer!
Should not have
• Clutter & busy designs

```html
<!DOCTYPE html>
<html lang="en">
<head>
<meta charset="utf-8">
<title>Headland Retreats – DL Flyer</title>
<link href="https://fonts.googleapis.com/css2?family=Questrial&family=Poppins:wght@300;600&display=swap" rel="stylesheet">
<style>
  :root{
    --teal:#33b8a4;
    --teal-tint:#d6f1ec;
    --ink:#2b2b2b;
    --paper:#ffffff;
    --stage:#e9ebec;
    --night:#3b2f8f;
    --violet:#7d6fc7;
    --pool:#2f8ef0;
    --glow:#e9b466;
  }
  *{box-sizing:border-box;margin:0;padding:0}
  html,body{width:1200px;height:870px;overflow:hidden}
  body{background:var(--stage);font-family:"Questrial",sans-serif;color:var(--ink);position:relative}

  .flyer{position:absolute;left:190px;width:820px;height:386px;overflow:hidden;background:var(--paper);box-shadow:0 4px 14px rgba(0,0,0,.15)}
  .flyer--front{top:34px}
  .flyer--back{top:450px}

  /* front */
  .hero-photo{position:absolute;inset:0;
    background:
      radial-gradient(ellipse 45% 60% at 18% 78%, rgba(233,180,102,.95), rgba(233,180,102,0) 70%),
      radial-gradient(ellipse 40% 55% at 78% 82%, rgba(47,142,240,.95), rgba(47,142,240,0) 70%),
      linear-gradient(160deg,var(--night) 0%,var(--violet) 45%,#4b3f9e 100%);}
  .brand-band{position:absolute;inset:0;width:100%;height:100%}
  .brand-name{position:absolute;right:34px;top:44px;display:flex;align-items:center;gap:10px;
    color:var(--paper);font-size:24px;line-height:1}
  .brand-name::before{content:"";width:14px;height:14px;border-radius:50%;background:var(--paper);flex:none}
  .hero-title{position:absolute;left:330px;top:280px;color:var(--paper)}
  .hero-title h1{font-family:"Poppins",sans-serif;font-weight:600;font-size:40px;line-height:1;letter-spacing:.5px}
  .hero-title p{font-family:"Poppins",sans-serif;font-weight:300;font-size:19px;margin-top:4px}

  /* back */
  .pattern-strip{position:absolute;top:0;bottom:44px;width:62px;background:var(--teal-tint)}
  .pattern-strip--left{left:0}
  .pattern-strip--right{right:0}
  .back-copy{position:absolute;left:92px;right:92px;top:40px;font-size:12.5px;line-height:1.45}
  .back-copy h2{font-family:"Poppins",sans-serif;font-weight:600;color:var(--teal);font-size:15px;margin-bottom:4px}
  .back-copy p{margin-bottom:8px}
  .back-copy strong{font-weight:700}
  .service-list{list-style:none;margin:2px 0 0 14px}
  .service-list li{display:flex;align-items:center;gap:8px;margin-bottom:3px}
  .service-list li::before{content:"";width:8px;height:8px;border-radius:50%;border:1.5px solid var(--teal);flex:none}
  .contact-prompt{position:absolute;left:0;right:0;top:258px;text-align:center;font-family:"Poppins",sans-serif;font-weight:600;color:var(--teal);font-size:14px;line-height:1.35}
  .contact-bar{position:absolute;left:0;right:0;bottom:0;height:44px;background:var(--teal);display:flex;align-items:center;justify-content:center;gap:26px;font-size:13px;color:var(--ink);font-weight:700}
  .contact-item{display:flex;align-items:center;gap:6px}
  .contact-item svg{width:13px;height:13px;fill:var(--ink)}
</style>
</head>
<body>

<section class="flyer flyer--front">
  <div class="hero-photo" role="img" aria-label="Photo of a modern luxury holiday home at dusk with lit windows beside an illuminated swimming pool"></div>
  <svg class="brand-band" viewBox="0 0 820 386" aria-hidden="true">
    <path d="M505 0 Q640 150 820 170 L820 0 Z" fill="var(--teal)"/>
    <path d="M505 0 Q640 150 820 170" fill="none" stroke="var(--paper)" stroke-width="3"/>
  </svg>
  <p class="brand-name">Headland Retreats</p>
  <div class="hero-title">
    <h1>Holiday Rental</h1>
    <p>Management with a difference</p>
  </div>
</section>

<section class="flyer flyer--back">
  <div class="pattern-strip pattern-strip--left" role="img" aria-label="Decorative teal geometric pattern border"></div>
  <div class="pattern-strip pattern-strip--right" role="img" aria-label="Decorative teal geometric pattern border"></div>
  <div class="back-copy">
    <h2>What we do differently!</h2>
    <p>Rather than relying upon a key safe or a central pick-up destination, a ‘<strong>Headland Retreats</strong>’ staff member will greet guests upon arrival.</p>
    <p>Our ‘<strong>Meet &amp; Greet</strong>’ service provides home owners with an increased level of Security and also allows us to:</p>
    <ul class="service-list">
      <li>Prepare the home for their arrival ( lights, heaters, music etc.)</li>
      <li>Establish a rapport &amp; help facilitate future bookings.</li>
      <li>Reiterate their responsibilities to ensure the return of their bond.</li>
    </ul>
  </div>
  <p class="contact-prompt">If you’d like to know what your property could achieve<br>or require additional information, please contact us on:</p>
  <div class="contact-bar">
    <span class="contact-item"><svg viewBox="0 0 24 24"><path d="M6.6 10.8a15 15 0 0 0 6.6 6.6l2.2-2.2a1 1 0 0 1 1-.25 11.4 11.4 0 0 0 3.6.57 1 1 0 0 1 1 1V20a1 1 0 0 1-1 1A17 17 0 0 1 3 4a1 1 0 0 1 1-1h3.5a1 1 0 0 1 1 1c0 1.25.2 2.45.57 3.57a1 1 0 0 1-.25 1z"/></svg>(03) 5550 2174</span>
    <span class="contact-item"><svg viewBox="0 0 24 24"><path d="M2 5h20v14H2z M2 5l10 8 10-8"/></svg>stay@headlandretreats.com.au</span>
    <span class="contact-item"><svg viewBox="0 0 24 24"><circle cx="12" cy="12" r="10"/></svg>headlandretreats.com.au</span>
    <span class="contact-item">PO Box 48, Harbourvale Victoria 3999</span>
  </div>
</section>

</body>
</html>
```